Clean Modern Skin Product branding/ label.

I need a label for a skincare line. The company is Dermaloft but product names will vary. A couple products to list are:
Sensitive Cleanser, Lumeno, Repair, Halo up, Mendora, Mendora Plus, Mendora Intense, Tavelo, Balance and Vivanto.

I would like the color scheme to be muted greens, grays, tourquise. The bottles are white, boston shaped with pumps, and ounces are 2, 4, 8, 16 ounces. When I choose the design, I can give you exact label sizes. Along with the ingredience already on the product label.

The look I desire is clean, minimal. A modern, organic look. Ideas that come to mind are a Veloraine,https://www.veloraine-example.com/product/2846/37204/3-step/step-2-exfoliate/clarifying-lotion-1 and the simplicity of Bo Tarn.

Both styles high light the name, in this case Dermaloft, and then the specific product.

My product is clean utilizing pure ingredients rather that a bunch fillers and binders. When I work with my clients I normally will say we need to "restore the balance" from over use of harsh products. That is why this lines works. It restores the skin to it's natural state. The process is simple, so I would like the label to reflect that simplicity.

Target Market(s)

Anyone with sensitive skin. So gender neutral

Industry/Entity Type

Skin Care Product

Font styles to use
Serif
Sans Serif
Decorative

Colors
acd037
33b8a4
fcfefd
85cae6
d3d3d3

Requirements
Must have
• Logo, name of product and color identity for cleanser, Active products, moisturizers
• I am thinking we could have one color for a cleanser and a space where I can put a sticker on which cleanser it is. Acne Cleasner, Sensitive Cleanser, and Cleanser.
Nice to have
• Not sure....suprise me. I would like the font to stay the same on the DERMALOFT, but you can change color, or color of leaf.
Should not have
• Too busy, too crowded or look like every other skincare line

```html
<!DOCTYPE html>
<html lang="en">
<head>
<meta charset="utf-8">
<title>Dermaloft – Sensitive Cleanser label</title>
<link rel="stylesheet" href="https://fonts.googleapis.com/css2?family=Didact+Gothic&display=swap">
<style>
  :root {
    --backdrop: #1f9c9a;
    --label-white: #ffffff;
    --swash-grey: #c9d0ce;
    --wordmark-grey: #6f7478;
    --product-ink: #1c1f22;
    --rule-blue: #3f6f8c;
    --leaf-green: #4fdc2c;
  }
  * { margin: 0; padding: 0; box-sizing: border-box; }
  html, body {
    width: 1200px;
    height: 1200px;
    overflow: hidden;
    background: var(--backdrop);
    font-family: "Didact Gothic", "Questrial", sans-serif;
  }
  .label {
    position: absolute;
    left: 190px;
    top: 128px;
    width: 820px;
    height: 944px;
    background: var(--label-white);
    box-shadow: 0 6px 18px rgba(0, 0, 0, 0.18);
  }
  .brand-swash {
    position: absolute;
    left: 46px;
    top: 120px;
    width: 720px;
    height: 200px;
    background: linear-gradient(90deg,
      rgba(201, 208, 206, 0.55) 0%,
      var(--swash-grey) 10%,
      var(--swash-grey) 88%,
      rgba(201, 208, 206, 0.45) 100%);
    border-radius: 30px 60px 20px 40px;
  }
  .brand-name {
    position: absolute;
    left: 0;
    top: 150px;
    width: 100%;
    text-align: center;
    font-size: 112px;
    line-height: 1;
    letter-spacing: -1px;
    color: var(--wordmark-grey);
  }
  .product-name {
    position: absolute;
    left: 153px;
    top: 347px;
    width: 514px;
    height: 70px;
    border-top: 1.5px solid var(--rule-blue);
    border-bottom: 1.5px solid var(--rule-blue);
    text-align: center;
    font-size: 56px;
    line-height: 66px;
    color: var(--product-ink);
  }
  .tagline {
    position: absolute;
    left: 0;
    top: 770px;
    width: 100%;
    text-align: center;
    font-size: 44px;
    line-height: 1;
    letter-spacing: 0.5px;
    color: var(--leaf-green);
  }
</style>
</head>
<body>
  <main class="label">
    <div class="brand-swash" role="img" aria-label="Soft grey painted brush swash behind the brand name"></div>
    <h1 class="brand-name">Dermaloft</h1>
    <h2 class="product-name">Sensitive Cleanser</h2>
    <p class="tagline">restore the balance</p>
  </main>
</body>
</html>
```